Brisk Coatings business card for residential and commercial painting

A clean, professional design. Easy to read
Eye catching and elegant
Front could have some color variations
On the back of card I would like all black with signature logo

*Attached is my current business card and the items I want displayed

Contact Information for Business Card

Email, phone number, website, and owner name

Font styles to use
Serif

Requirements
Must have
• My logo with cool design and perhaps some paint splatter

```html
<!DOCTYPE html>
<html lang="en">
<head>
<meta charset="utf-8">
<title>Brisk Coatings Business Card</title>
<link href="https://fonts.googleapis.com/css2?family=Oswald:wght@500;700&family=Roboto:wght@400&display=swap" rel="stylesheet">
<style>
  :root {
    --backdrop: #8a8a8a;
    --card-dark: #3a3a3c;
    --card-light: #ffffff;
    --brand-blue: #1174bd;
    --ink-white: #ffffff;
    --ink-dark: #3a3a3c;
    --brush-white: #f4f4f4;
    --faint-blue: #e3eef8;
    --faint-grey: #ececec;
  }
  * { margin: 0; padding: 0; box-sizing: border-box; }
  html, body { width: 1200px; height: 866px; overflow: hidden; }
  body {
    background: var(--backdrop);
    font-family: "Roboto", Arial, sans-serif;
    position: relative;
  }
  .card {
    position: absolute;
    top: 284px;
    width: 520px;
    height: 297px;
    overflow: hidden;
    box-shadow: 0 6px 14px rgba(0,0,0,0.35);
  }
  .card-front { left: 50px; background: var(--card-dark); }
  .card-back { left: 630px; background: var(--card-light); }

  .wordmark {
    font-family: "Oswald", "Arial Narrow", sans-serif;
    font-weight: 700;
    text-transform: uppercase;
    letter-spacing: 1px;
    display: flex;
    align-items: center;
    gap: 10px;
  }
  .wordmark-dot {
    width: 14px; height: 14px; border-radius: 50%;
    background: var(--brand-blue);
  }
  .card-front .wordmark {
    position: absolute; left: 30px; top: 26px;
    font-size: 40px; color: var(--ink-white);
  }
  .owner-name {
    position: absolute; left: 30px; top: 92px;
    font-family: "Oswald", "Arial Narrow", sans-serif;
    font-weight: 500; font-size: 26px; color: var(--brand-blue);
  }
  .owner-title {
    position: absolute; left: 30px; top: 128px;
    font-size: 14px; color: var(--ink-white); letter-spacing: 0.5px;
  }
  .contact-list {
    position: absolute; left: 30px; top: 160px;
    list-style: none;
  }
  .contact-item {
    display: flex; align-items: center; gap: 8px;
    font-size: 13px; color: var(--ink-white);
    line-height: 20px; letter-spacing: 0.4px;
  }
  .contact-icon { width: 13px; height: 13px; flex: none; }

  .paint-wave { position: absolute; right: 0; bottom: 0; width: 520px; height: 297px; }
  .brush-art {
    position: absolute; left: 250px; top: 150px;
    width: 250px; height: 64px; border-radius: 8px 32px 32px 8px;
    background: linear-gradient(90deg, var(--brush-white), #d9d9d9);
  }

  .price-label {
    position: absolute; left: 30px; top: 26px;
    font-family: "Oswald", "Arial Narrow", sans-serif;
    font-weight: 500; font-size: 18px; color: var(--ink-dark);
  }
  .card-back .wordmark {
    position: absolute; left: 30px; top: 180px;
    font-size: 30px; color: var(--ink-dark);
  }
  .brush-faint {
    position: absolute; right: 20px; top: 110px;
    width: 270px; height: 70px; border-radius: 8px 34px 34px 8px;
    background: linear-gradient(90deg, var(--faint-grey), var(--faint-blue));
  }
</style>
</head>
<body>
  <section class="card card-front">
    <svg class="paint-wave" viewBox="0 0 520 297" aria-hidden="true">
      <path d="M180 297 C260 250 330 215 400 205 C450 198 490 180 520 150 L520 297 Z" fill="var(--brand-blue)"/>
    </svg>
    <div class="brush-art" role="img" aria-label="White paintbrush dipped in blue paint"></div>

    <div class="wordmark"><span class="wordmark-dot"></span>Brisk Coatings</div>
    <div class="owner-name">Marco "Mac"</div>
    <div class="owner-title">Owner-Licensed &amp; Insured</div>
    <ul class="contact-list">
      <li class="contact-item">
        <svg class="contact-icon" viewBox="0 0 16 16"><path d="M4 1 L6.5 4.5 L5 6.5 C6 8.5 7.5 10 9.5 11 L11.5 9.5 L15 12 L13 15 C7 14 2 9 1 3 Z" fill="var(--brand-blue)"/></svg>
        555.014.2290
      </li>
      <li class="contact-item">
        <svg class="contact-icon" viewBox="0 0 16 16"><rect x="1" y="3" width="14" height="10" fill="var(--brand-blue)"/><path d="M1 3 L8 9 L15 3" fill="none" stroke="var(--card-dark)" stroke-width="1.4"/></svg>
        briskcoatings@mail.com
      </li>
      <li class="contact-item">
        <svg class="contact-icon" viewBox="0 0 16 16"><circle cx="8" cy="8" r="6.5" fill="none" stroke="var(--brand-blue)" stroke-width="1.5"/><ellipse cx="8" cy="8" rx="3" ry="6.5" fill="none" stroke="var(--brand-blue)" stroke-width="1.2"/><path d="M1.5 8 H14.5" stroke="var(--brand-blue)" stroke-width="1.2"/></svg>
        www.briskcoatings.com
      </li>
    </ul>
  </section>

  <section class="card card-back">
    <div class="price-label">Price:</div>
    <div class="brush-faint" role="img" aria-label="Faint paintbrush decoration"></div>
    <div class="wordmark"><span class="wordmark-dot"></span>Brisk Coatings</div>
  </section>
</body>
</html>
```